Marlow Sail Works President Business Card Carbon fiber catamarans

Hi.. I need a new business card design.. I am the President of a high tech yacht builder. We build Carbon Fiber go fast catamarans... Maybe we use the file I am sharing to you as the back of the card.. We need to look cool and crisp ...

Target Market(s)

Affluent People who will purchase a cool yacht

Industry/Entity Type

Custom Yacht Builder

Contact Information for Business Card

Dean Pellway , President, 731.508.2164 USA

Font styles to use
Serif

Requirements
Must have
• the clean crisp cool feel
Nice to have
• clean and crisp
Should not have
• Bold ugly

```html
<!DOCTYPE html>
<html lang="en">
<head>
<meta charset="utf-8">
<title>Marlow Sail Works — Business Card</title>
<link rel="stylesheet" href="https://fonts.googleapis.com/css2?family=Michroma&display=swap">
<style>
  :root {
    --page-bg: #2a2a2a;
    --card-dark: #0b0b0b;
    --card-mid: #1a1a1a;
    --silver: #d9d9d9;
    --silver-soft: #bdbdbd;
    --silver-dim: #8f8f8f;
  }
  * { box-sizing: border-box; margin: 0; padding: 0; }
  html, body {
    width: 1200px;
    height: 1015px;
    overflow: hidden;
    background: radial-gradient(ellipse at center, #343434 0%, var(--page-bg) 55%, #161616 100%);
    font-family: "Michroma", sans-serif;
    color: var(--silver);
  }
  .sheet {
    position: relative;
    width: 1200px;
    height: 1015px;
  }
  .card {
    position: absolute;
    left: 290px;
    width: 620px;
    height: 354px;
    border-radius: 3px;
    overflow: hidden;
    box-shadow: 0 14px 30px rgba(0,0,0,0.55);
  }
  .card--front { top: 120px; }
  .card--back { top: 530px; }
  .card__surface {
    position: absolute;
    inset: 0;
    background: linear-gradient(135deg, var(--card-mid) 0%, var(--card-dark) 60%, #050505 100%);
  }
  .brand {
    position: absolute;
    display: flex;
    align-items: center;
    gap: 16px;
  }
  .brand__dot {
    width: 14px;
    height: 14px;
    border-radius: 50%;
    background: var(--silver);
    flex: none;
  }
  .brand__name {
    font-size: 24px;
    letter-spacing: 0.16em;
    text-transform: uppercase;
    color: var(--silver);
    white-space: nowrap;
  }
  .card--front .brand {
    left: 50%;
    top: 50%;
    transform: translate(-50%, -50%);
  }
  .card--back .brand {
    left: 52px;
    top: 50px;
  }
  .card--back .brand__name { font-size: 21px; }
  .person {
    position: absolute;
    left: 82px;
    top: 118px;
  }
  .person__name {
    font-size: 17px;
    letter-spacing: 0.1em;
    color: var(--silver);
  }
  .person__title {
    margin-top: 6px;
    font-size: 12px;
    letter-spacing: 0.14em;
    color: var(--silver-soft);
  }
  .contact {
    position: absolute;
    left: 82px;
    top: 196px;
    list-style: none;
  }
  .contact__item {
    display: flex;
    align-items: center;
    gap: 12px;
    font-size: 11px;
    letter-spacing: 0.1em;
    color: var(--silver);
    height: 24px;
  }
  .contact__item--address { margin-top: 12px; }
  .contact__icon {
    width: 13px;
    height: 13px;
    flex: none;
    fill: none;
    stroke: var(--silver-soft);
    stroke-width: 1.4;
  }
</style>
</head>
<body>
<main class="sheet">

  <section class="card card--front" aria-label="Card front">
    <div class="card__surface" role="img" aria-label="Black carbon fiber weave texture"></div>
    <div class="brand">
      <span class="brand__dot"></span>
      <span class="brand__name">Marlow Sail Works</span>
    </div>
  </section>

  <section class="card card--back" aria-label="Card back">
    <div class="card__surface" role="img" aria-label="Black carbon fiber weave texture"></div>
    <div class="brand">
      <span class="brand__dot"></span>
      <span class="brand__name">Marlow Sail Works</span>
    </div>

    <div class="person">
      <p class="person__name">Dean Pellway</p>
      <p class="person__title">President</p>
    </div>

    <ul class="contact">
      <li class="contact__item">
        <svg class="contact__icon" viewBox="0 0 16 16" aria-hidden="true"><path d="M4 1.5l2.5 3-1.5 1.8c.8 1.8 2 3 3.7 3.7L10.5 8.5l3 2.5-1.5 2.5C7 13.5 2.5 9 2.5 3z"/></svg>
        <span>731.508.2164</span>
      </li>
      <li class="contact__item">
        <svg class="contact__icon" viewBox="0 0 16 16" aria-hidden="true"><rect x="1.5" y="3.5" width="13" height="9"/><path d="M1.5 3.5L8 9l6.5-5.5"/></svg>
        <span>info@marlowsail.com</span>
      </li>
      <li class="contact__item">
        <svg class="contact__icon" viewBox="0 0 16 16" aria-hidden="true"><circle cx="8" cy="8" r="6.5"/><ellipse cx="8" cy="8" rx="2.8" ry="6.5"/><path d="M1.5 8h13"/></svg>
        <span>www.marlowsailworks.com</span>
      </li>
      <li class="contact__item contact__item--address">
        <svg class="contact__icon" viewBox="0 0 16 16" aria-hidden="true"><path d="M8 15s-5-5.2-5-8.8a5 5 0 0110 0C13 9.8 8 15 8 15z"/><circle cx="8" cy="6.2" r="1.7"/></svg>
        <span>Rhode Island 02840, USA</span>
      </li>
    </ul>
  </section>

</main>
</body>
</html>
```